Collectibles expert needs a new business card design.

My current business card makes me look to high end. It may even make me look arrogant or too stuffy. I do work with high end clients and their items but most of my business is with average people with average items. My business name is Walter Brennick's Old Orchard Salvage Co. The idea was that I mine the streets helping people discover the treasures buried in their homes. That could be art, jewelry, coins, etc. The name and an older logo I used does not make immediate sense to most people. I tried to go with just my picture and name and that is the current card I am changing. I help people who need to downsize. Whether they are getting rid of one item, a collection or a house full of items I help them discover what they have, what it is worth and what are the best ways we can get the most for them. This may be a combination of estate sale (which I dont do) auction or sell directly to a dealer or collector. Usually it is a combination of these. My main goal is to help make sure they dont accidently sell a Picasso painting in a garage sale. I am uploading a copy of my old card and the old logo I used to use but the winning card design will need to be much different than these. You can learn a little more about me at www.walterjbrennick.example, www.oldorchardsalv.example and www.facebook.com/oosalco. I hope someone can look at what I do and come up with a very unique design that will be equally effective if my client is high income or if my client is low to mid income. I do not care if it is a one or two sided card as long as it conveys my contact information and a good representation of what I do.

Target Market(s)

People who are getting rid of items. These can be elderly couples or individuals that are moving to an active living community and will have less space so they need to sell items. This can also include the children of elder parents that dont want their stuff and want to find solutions to help them get rid of their items.

Contact Information for Business Card

The card should have my business name Walter Brennick's Old Orchard Salvage Co., phone number 555-302-71938, email walter@oldorchardsalvage.example and website www.oldorchardsalvage.example. Would also like to include Buyer, Broker, Consultant and Appraiser. We can put Walter J. Brennick, ISA on the opposite side of the company name since it includes my name as well.

Font styles to use
Sans Serif

Colors

Designer to choose colors to be used in the design.

Requirements
Must have
• My project must have a professional look. It must not alienate low income clients and should still be appealing to high value clients.

```html
<!DOCTYPE html>
<html lang="en">
<head>
<meta charset="utf-8">
<title>Walter J. Brennick — Business Card</title>
<link rel="stylesheet" href="https://fonts.googleapis.com/css2?family=Oswald:wght@500;600&family=Open+Sans:wght@400&display=swap">
<style>
  :root {
    --page: #e8e8eb;
    --navy: #1f3f60;
    --slate: #58585a;
    --white: #ffffff;
    --disc-light: #fbfbfb;
    --disc-shade: #d6d7d9;
    --mark-grey: #6a6a6c;
  }
  * { margin: 0; padding: 0; box-sizing: border-box; }
  html, body {
    width: 1200px;
    height: 900px;
    overflow: hidden;
    background: var(--page);
  }
  .card {
    position: absolute;
    left: 100px;
    top: 140px;
    width: 1000px;
    height: 620px;
    background: linear-gradient(to right, var(--navy) 0 678px, var(--slate) 678px 100%);
    box-shadow: 0 10px 30px rgba(0,0,0,0.18);
    overflow: hidden;
  }
  .owner {
    position: absolute;
    left: 43px;
    top: 66px;
    color: var(--white);
  }
  .owner-name {
    font-family: "Oswald", sans-serif;
    font-weight: 500;
    font-size: 35px;
    line-height: 1.1;
    text-transform: uppercase;
    letter-spacing: 0.2px;
  }
  .owner-roles {
    font-family: "Open Sans", sans-serif;
    font-size: 26px;
    line-height: 1.42;
    margin-top: 6px;
  }
  .contacts {
    position: absolute;
    left: 43px;
    top: 440px;
    list-style: none;
    color: var(--white);
    font-family: "Open Sans", sans-serif;
    font-size: 26px;
    line-height: 37px;
  }
  .contacts li { display: flex; align-items: center; }
  .contacts svg { width: 22px; height: 22px; margin-right: 10px; fill: var(--white); flex: none; }
  .brand-disc {
    position: absolute;
    left: 417px;
    top: 40px;
    width: 540px;
    height: 540px;
    border-radius: 50%;
    background: radial-gradient(circle at 40% 35%, var(--disc-light) 0%, #eeeeef 55%, var(--disc-shade) 100%);
  }
  .brand-mark {
    position: absolute;
    left: 50%;
    top: 95px;
    width: 150px;
    height: 150px;
    margin-left: -75px;
    border-radius: 50%;
    border: 9px solid var(--mark-grey);
  }
  .brand-name {
    position: absolute;
    left: 0;
    right: 0;
    top: 292px;
    text-align: center;
    color: var(--navy);
    font-family: "Oswald", sans-serif;
    font-weight: 600;
    text-transform: uppercase;
    line-height: 1.15;
  }
  .brand-name .line-owner { display: block; font-size: 34px; letter-spacing: 1px; }
  .brand-name .line-company { display: block; font-size: 44px; }
</style>
</head>
<body>
  <div class="card">
    <div class="owner">
      <div class="owner-name">Walter J. Brennick, ISA</div>
      <div class="owner-roles">Buyer, Broker, Consultant<br>and Appraiser</div>
    </div>

    <ul class="contacts">
      <li>
        <svg viewBox="0 0 24 24" aria-hidden="true"><path d="M6.6 10.8a15.1 15.1 0 0 0 6.6 6.6l2.2-2.2c.3-.3.7-.4 1-.2 1.1.4 2.3.6 3.6.6.6 0 1 .4 1 1V20c0 .6-.4 1-1 1A17 17 0 0 1 3 4c0-.6.4-1 1-1h3.5c.6 0 1 .4 1 1 0 1.3.2 2.5.6 3.6.1.3 0 .7-.2 1z"/></svg>
        555-302-71938
      </li>
      <li>
        <svg viewBox="0 0 24 24" aria-hidden="true"><path d="M2 5h20v14H2z M4 7v.4l8 5 8-5V7l-8 5z" fill-rule="evenodd"/></svg>
        www.oldorchardsalvage.example
      </li>
      <li>
        <svg viewBox="0 0 24 24" aria-hidden="true"><circle cx="12" cy="12" r="10"/><path d="M7 8c2 0 3 1 3 2s-1 2 0 3 2 1 2 3-1 3-1 4M14 4c0 2 1 3 3 3s3 1 3 2" stroke="var(--navy)" stroke-width="1.8" fill="none"/></svg>
        walter@oldorchardsalvage.example
      </li>
    </ul>

    <div class="brand-disc">
      <div class="brand-mark" aria-hidden="true"></div>
      <div class="brand-name">
        <span class="line-owner">Walter Brennick's</span>
        <span class="line-company">Old Orchard Salvage Co.</span>
      </div>
    </div>
  </div>
</body>
</html>
```